Fern Hollow Academy business card

we need to incorporate our school logo, name, address onto a great new school business card for all our staff - I included a lot of detail below under must haves and I included 3 business card samples below also that give a flavour of what I want - I would like to include a great graphic on at least one side of the card that represents education -

Target Market(s)

this business card will need to be attractive to parents of all ages but especially millennial parents and even high school students who may influence parents to chose Fern Hollow Academy

Industry/Entity Type

Education

Contact Information for Business Card

should contain core value words "Curiosity kindness courage growth"
will need out school name, Fern Hollow Academy to be present, address 7318 Marwick Avenue, Maplecrest, British Columbia K3R8P1
telephone 604.781.2937 Ext. 216
first card will need my name on it, Marisol Thenkley, Director of Development & Operations
also web address of fernhollowacademy.example

Font styles to use
Other font styles liked:
• Tw Cent MT

Requirements
Must have
• a fresh modern look for a private school environment that appeals to parents looking for great education - must use school logo, and incorporate colours navy blue, CMYK 100, 60, 0, 56 and burgundy CMYK 27, 98, 81, 50
• below I uploaded 3 business card layouts that look interesting to me - I'd like to incorporate some great school photos into the design - I tried to upload some school photos that we have, that the files are too large apparently? so I could send a link to Filecrate or something like that to share great high res pics that would look nice - we are kindergarten to Gr. 12 school, so I would like to include images that would represent great education at any age.
Nice to have
• spot colour would be nice as an option for printing for maybe key administrator business cards, while the rest would be basic printing

```html
<!DOCTYPE html>
<html lang="en">
<head>
<meta charset="utf-8">
<title>Fern Hollow Academy – Business Card</title>
<link href="https://fonts.googleapis.com/css2?family=Source+Sans+3:wght@400;600;700;800&display=swap" rel="stylesheet">
<style>
  :root {
    --navy: #0b2f6b;
    --burgundy: #7b1a2c;
    --ink: #2b2b2b;
    --paper: #ffffff;
    --backdrop: #e9e7e4;
  }
  * { box-sizing: border-box; margin: 0; padding: 0; }
  html, body { width: 1200px; height: 844px; overflow: hidden; }
  body {
    background: var(--backdrop);
    font-family: "Source Sans 3", "Segoe UI", sans-serif;
    color: var(--ink);
    display: flex;
    align-items: center;
    justify-content: center;
    gap: 60px;
  }
  .card {
    position: relative;
    width: 520px;
    height: 297px;
    overflow: hidden;
    box-shadow: 0 6px 18px rgba(0,0,0,0.18);
  }
  .card-front { background: var(--paper); }
  .brand {
    position: absolute;
    top: 26px;
    right: 30px;
    display: flex;
    align-items: center;
    gap: 14px;
  }
  .brand-mark {
    width: 66px; height: 66px;
    border-radius: 50%;
    background: var(--navy);
  }
  .brand-name {
    font-weight: 800;
    color: var(--burgundy);
    font-size: 30px;
    line-height: 0.9;
    text-transform: uppercase;
    letter-spacing: 0.5px;
  }
  .tagline {
    position: absolute;
    top: 104px;
    right: 30px;
    font-weight: 700;
    font-size: 15px;
    color: var(--ink);
  }
  .rule {
    position: absolute;
    left: 0; right: 0;
    height: 2px;
    background: var(--navy);
  }
  .rule-top { top: 128px; }
  .rule-mid { top: 210px; height: 1.5px; }
  .person {
    position: absolute;
    left: 26px;
    top: 160px;
  }
  .person-name { font-size: 21px; font-weight: 700; line-height: 1.1; }
  .person-name .first { color: var(--navy); }
  .person-name .last { color: var(--burgundy); }
  .person-title { font-size: 14px; color: var(--ink); margin-top: 2px; }
  .contact {
    position: absolute;
    left: 26px;
    top: 218px;
    list-style: none;
    font-size: 14px;
    line-height: 23px;
  }
  .contact li { display: flex; align-items: center; gap: 8px; }
  .contact svg { width: 12px; height: 12px; fill: var(--burgundy); flex: none; }
  .contact .address { padding-left: 20px; }
  .card-back { background: var(--burgundy); }
  .card-back svg { display: block; }
</style>
</head>
<body>

<section class="card card-front" aria-label="Business card front">
  <div class="brand">
    <span class="brand-mark" aria-hidden="true"></span>
    <span class="brand-name">Fern Hollow<br>Academy</span>
  </div>
  <p class="tagline">Curiosity kindness courage growth</p>
  <div class="rule rule-top"></div>

  <div class="person">
    <p class="person-name"><span class="first">Marisol</span> <span class="last">Thenkley</span></p>
    <p class="person-title">Director of Development &amp; Operations</p>
  </div>
  <div class="rule rule-mid"></div>

  <ul class="contact">
    <li>
      <svg viewBox="0 0 24 24" aria-hidden="true"><path d="M6.6 10.8a15.1 15.1 0 0 0 6.6 6.6l2.2-2.2c.3-.3.7-.4 1-.2 1.1.4 2.3.6 3.6.6.6 0 1 .4 1 1V20c0 .6-.4 1-1 1A17 17 0 0 1 3 4c0-.6.4-1 1-1h3.5c.6 0 1 .4 1 1 0 1.3.2 2.5.6 3.6.1.3 0 .7-.2 1z"/></svg>
      555.781.2937 Ext. 216
    </li>
    <li>
      <svg viewBox="0 0 24 24" aria-hidden="true"><circle cx="12" cy="12" r="11"/></svg>
      fernhollowacademy.example
    </li>
    <li class="address">7318 Marwick Avenue, Maplecrest, British Columbia K3R8P1</li>
  </ul>
</section>

<section class="card card-back" aria-label="Business card back">
  <svg width="520" height="297" viewBox="0 0 520 297">
    <defs>
      <linearGradient id="photo-tones" x1="0" y1="0" x2="1" y2="1">
        <stop offset="0" stop-color="#3a3a3a"/>
        <stop offset="0.45" stop-color="#1c1c22"/>
        <stop offset="0.8" stop-color="#8a2a22"/>
        <stop offset="1" stop-color="#c23a24"/>
      </linearGradient>
    </defs>
    <rect width="520" height="297" fill="var(--burgundy)"/>
    <path role="img" aria-label="Photo of graduating students in caps and gowns"
          d="M0 0 H200 V22 H270 V58 H340 V98 H400 V150 H520 V297 H0 Z"
          fill="url(#photo-tones)" stroke="#ffffff" stroke-width="3" stroke-linejoin="miter"/>
  </svg>
</section>

</body>
</html>
```